Outdoor Banners for Shopping Center

I need outdoor banners for a small California Shopping Center (Calloway Pines Plaza). You must include the property logo. Each parking lot pole will have 2 banners -- one on each side of the pole so the design should take that into account. Use bright colors… something that will work well with the logo. Size for each banner is 30"w x 96"h. It should be bold and easy to read (if you include any additional text).

Target Market(s)

Middle class shoppers.

Industry/Entity Type

Graphic Design

Font styles to use
Serif
Sans Serif

Requirements
Must have
• The property logo.

```html
<!DOCTYPE html>
<html lang="en">
<head>
<meta charset="utf-8">
<title>Calloway Pines Plaza – Pole Banners</title>
<link rel="stylesheet" href="https://fonts.googleapis.com/css2?family=Anton&display=swap">
<style>
  :root {
    --page: #ffffff;
    --sun-yellow: #fff200;
    --hot-magenta: #ff00ff;
    --ink: #111111;
    --white: #ffffff;
    --navy: #1b2a8c;
    --swirl-pink: #f25ad6;
    --swirl-violet: #8a4fe0;
    --swirl-lime: #b8ec5a;
    --swirl-orange: #f7a21b;
    --swirl-cream: #f9e2a6;
  }
  * { margin: 0; padding: 0; box-sizing: border-box; }
  html, body {
    width: 849px;
    height: 1200px;
    overflow: hidden;
    background: var(--page);
  }
  .canvas {
    position: relative;
    width: 849px;
    height: 1200px;
    background: var(--page);
    font-family: "Anton", "Oswald", sans-serif;
  }
  .banner {
    position: absolute;
    top: 82px;
    width: 321px;
    height: 1031px;
    overflow: hidden;
  }
  .banner--yellow { left: 78px; background: var(--sun-yellow); }
  .banner--magenta { left: 456px; background: var(--hot-magenta); }

  .property-name {
    position: absolute;
    left: 0;
    width: 100%;
    text-align: center;
    font-family: "Anton", sans-serif;
    font-weight: 400;
    font-size: 38px;
    line-height: 1.1;
    color: var(--navy);
    letter-spacing: 1px;
  }
  .property-name__dot {
    display: block;
    width: 22px;
    height: 22px;
    margin: 0 auto 10px;
    border-radius: 50%;
    background: var(--navy);
  }
  .banner--yellow .property-name { top: 62px; }
  .banner--magenta .property-name { top: 860px; }

  .swirl {
    position: absolute;
    left: 0;
    width: 100%;
  }
  .banner--yellow .swirl {
    top: 254px;
    height: 510px;
    background:
      radial-gradient(ellipse 55% 45% at 50% 50%, var(--swirl-violet) 0%, rgba(138,79,224,0) 60%),
      radial-gradient(ellipse 45% 60% at 60% 70%, var(--swirl-pink) 0%, rgba(242,90,214,0) 70%),
      radial-gradient(ellipse 45% 50% at 35% 30%, var(--swirl-pink) 0%, rgba(242,90,214,0) 70%),
      radial-gradient(ellipse 40% 40% at 75% 35%, var(--swirl-lime) 0%, rgba(184,236,90,0) 70%);
  }
  .banner--magenta .swirl {
    top: 239px;
    height: 605px;
    background:
      radial-gradient(ellipse 50% 40% at 50% 50%, var(--swirl-violet) 0%, rgba(138,79,224,0) 60%),
      radial-gradient(ellipse 45% 55% at 58% 70%, var(--swirl-orange) 0%, rgba(247,162,27,0) 70%),
      radial-gradient(ellipse 45% 55% at 40% 28%, var(--swirl-cream) 0%, rgba(249,226,166,0) 70%),
      radial-gradient(ellipse 40% 40% at 75% 40%, var(--swirl-lime) 0%, rgba(184,236,90,0) 70%);
  }

  .tagline {
    position: absolute;
    left: 0;
    width: 100%;
    text-align: center;
    font-family: "Anton", sans-serif;
    font-weight: 400;
    font-size: 54px;
    line-height: 1.22;
  }
  .banner--yellow .tagline { top: 830px; color: var(--ink); }
  .banner--magenta .tagline { top: 18px; color: var(--white); }
</style>
</head>
<body>
<main class="canvas">
  <section class="banner banner--yellow">
    <div class="property-name"><span class="property-name__dot"></span>Calloway Pines<br>Plaza</div>
    <div class="swirl" role="img" aria-label="Bright splash of pink, violet and lime droplet petals bursting outward"></div>
    <p class="tagline">A Great<br>Place to Be!</p>
  </section>

  <section class="banner banner--magenta">
    <p class="tagline">A Great<br>Place to Be!</p>
    <div class="swirl" role="img" aria-label="Bright splash of orange, cream, violet and lime droplet petals bursting outward"></div>
    <div class="property-name"><span class="property-name__dot"></span>Calloway Pines<br>Plaza</div>
  </section>
</main>
</body>
</html>
```